Quorva - corporate Business Card

We need a good look and innovative business card for a new start up company based in Los Angeles called "Quorva". We are in a payment business, including payment card, app, and ewallet. We are expert in online payment and Card not present (CNP) transaction.
We need an innovative, modern business card.

Our logo font is Aero Matics

Target Market(s)

Startup - Bank - Online Payment - Card Manufacturing

Industry/Entity Type

Startup

Contact Information for Business Card

phone: 555 014 7396 - Address: 4172 Marlowe blvd, Harlow Park, CA 90299

Requirements
Must have
• Message: innovative, professional, expert, high tech, trust, online payment expert, security
Nice to have
• no comment
Should not have
• no Comment

```html
<!DOCTYPE html>
<html lang="en">
<head>
<meta charset="utf-8">
<title>Quorva – Business Card</title>
<link href="https://fonts.googleapis.com/css2?family=PT+Sans:wght@400;700&display=swap" rel="stylesheet">
<style>
  :root {
    --brand-red: #b81f2f;
    --card-white: #ffffff;
    --text-grey: #4a4a4a;
    --strip-grey: #8f8f8f;
    --divider-grey: #c9c9c9;
    --backdrop: #e7e5e2;
    --faint-circle: rgba(255, 255, 255, 0.1);
  }
  * { margin: 0; padding: 0; box-sizing: border-box; }
  html, body {
    width: 1200px; height: 987px; overflow: hidden;
    background: var(--backdrop);
    font-family: "PT Sans", Arial, sans-serif;
  }
  .canvas { position: relative; width: 1200px; height: 987px; }

  .card {
    position: absolute; left: 293px; width: 615px; height: 349px;
    box-shadow: 0 2px 8px rgba(0,0,0,0.18);
    overflow: hidden;
  }
  .card--front { top: 131px; background: var(--card-white); }
  .card--back  { top: 506px; background: var(--brand-red); }

  .card__shapes { position: absolute; inset: 0; }

  /* front */
  .brand {
    position: absolute; left: 76px; top: 128px;
    display: flex; align-items: center; gap: 14px;
  }
  .brand__dot { width: 70px; height: 70px; border-radius: 50%; background: var(--brand-red); }
  .brand__name {
    font-size: 47px; font-weight: 700; color: var(--brand-red);
    line-height: 1; letter-spacing: 1px;
  }
  .divider {
    position: absolute; left: 332px; top: 70px; width: 1px; height: 186px;
    background: var(--divider-grey);
  }
  .contact { position: absolute; left: 359px; top: 80px; color: var(--text-grey); }
  .contact__name {
    font-size: 21px; font-weight: 700; color: var(--brand-red);
    line-height: 24px; letter-spacing: 0.5px;
  }
  .contact__title { font-size: 17px; line-height: 22px; }
  .contact__address { margin-top: 16px; font-size: 16px; line-height: 22px; }
  .contact__lines { margin-top: 11px; }
  .contact__line {
    display: flex; align-items: center; gap: 9px;
    font-size: 16px; line-height: 24px;
  }
  .contact__icon { width: 14px; height: 14px; flex: none; }

  .web--front {
    position: absolute; right: 31px; top: 316px;
    font-size: 15px; letter-spacing: 3.4px; color: var(--card-white);
  }

  /* back */
  .back-name {
    position: absolute; right: 44px; top: 240px;
    font-size: 61px; font-weight: 700; color: var(--card-white);
    line-height: 1; letter-spacing: 1.5px;
  }
  .web--back {
    position: absolute; right: 44px; top: 306px;
    font-size: 15px; letter-spacing: 3.6px; color: var(--card-white);
  }
</style>
</head>
<body>
<main class="canvas">

  <section class="card card--front" aria-label="Business card front">
    <svg class="card__shapes" width="615" height="349" viewBox="0 0 615 349" aria-hidden="true">
      <rect x="0" y="336" width="330" height="13" fill="var(--strip-grey)"/>
      <polygon points="352,310 615,310 615,349 318,349" fill="var(--brand-red)"/>
    </svg>

    <div class="brand">
      <span class="brand__dot"></span>
      <span class="brand__name">quorva</span>
    </div>

    <div class="divider"></div>

    <div class="contact">
      <p class="contact__name">DANIEL REYES</p>
      <p class="contact__title">CEO&amp;Founder</p>
      <p class="contact__address">4172 Marlowe blvd<br>Harlow Park, CA 90299</p>
      <div class="contact__lines">
        <p class="contact__line">
          <svg class="contact__icon" viewBox="0 0 24 24" aria-hidden="true">
            <path fill="var(--brand-red)" d="M6.6 10.8a15.1 15.1 0 0 0 6.6 6.6l2.2-2.2c.3-.3.7-.4 1-.2 1.1.4 2.3.6 3.6.6.6 0 1 .4 1 1V20c0 .6-.4 1-1 1A17 17 0 0 1 3 4c0-.6.4-1 1-1h3.5c.6 0 1 .4 1 1 0 1.3.2 2.5.6 3.6.1.3 0 .7-.2 1z"/>
          </svg>
          555 014 7396
        </p>
        <p class="contact__line">
          <svg class="contact__icon" viewBox="0 0 24 24" aria-hidden="true">
            <rect x="2" y="5" width="20" height="14" fill="var(--brand-red)"/>
            <path d="M2 5l10 8 10-8" fill="none" stroke="#fff" stroke-width="1.6"/>
          </svg>
          daniel@quorva.com
        </p>
      </div>
    </div>

    <p class="web--front">www.quorva.com</p>
  </section>

  <section class="card card--back" aria-label="Business card back">
    <svg class="card__shapes" width="615" height="349" viewBox="0 0 615 349" aria-hidden="true">
      <circle cx="173" cy="176" r="159" fill="var(--faint-circle)"/>
    </svg>
    <p class="back-name">quorva</p>
    <p class="web--back">www.quorva.com</p>
  </section>

</main>
</body>
</html>
```